New Business Card Design Project LORVANTI-Italy

we are LORVANTI-Italy
our company in the market for 3 years we are luxury cosmetic company and its about time for a facelift :)
i will like to have elegant luxurious and unique business card
that will give the person that get it a unique, luxurious and elegant impression
I'm VERY OPEN FOR NEW IDEAS , even duo i add a few files of things that i see on line and i like them

i add my logo as well
my website is LORVANTI.COM
(if you would like to see the main style that we have)

Target Market(s)

adult that have money :)

Industry/Entity Type

Business

Contact Information for Business Card

Name - Dario Lorvanti
Position - CEO and CO Founder
address - 4817 E Halvern
telephone - 555-384-1926
email - dario@lorvanti.com
fax - 555-384-1926
website - LORVANTI.COM

Colors
000000
959595
fbee3e
ffffff

Requirements
Must have
• big logo in GOLD color
• elegant look
• impressive
Nice to have
• not must but maybe classy pattern background
• not must but maybe emblem
• maybe clear plastic business card
Should not have
• colors
• images

```html
<!DOCTYPE html>
<html lang="en">
<head>
<meta charset="utf-8">
<title>LORVANTI Italy – Business Card</title>
<link rel="stylesheet" href="https://fonts.googleapis.com/css2?family=Roboto:wght@400;500;700&display=swap">
<style>
  :root {
    --backdrop: #232323;
    --card-white: #f3f3f3;
    --gold: #d4ab3f;
    --gold-light: #e2c466;
    --gold-deep: #cfa53e;
    --ink: #4a4a4a;
    --divider: #b5b5b5;
    --band-grey: #7a7a7a;
    --white: #ffffff;
  }
  html, body {
    margin: 0;
    padding: 0;
    width: 1200px;
    height: 960px;
    overflow: hidden;
    background: var(--backdrop);
    font-family: "Roboto", Arial, sans-serif;
  }
  .canvas {
    position: relative;
    width: 1200px;
    height: 960px;
  }
  .card {
    position: absolute;
    width: 600px;
    height: 342px;
    border-radius: 18px;
    overflow: hidden;
  }

  /* Front */
  .card-front {
    left: 314px;
    top: 114px;
    background: var(--card-white);
  }
  .brand-block {
    position: absolute;
    left: 80px;
    top: 78px;
    width: 206px;
    text-align: center;
  }
  .brand-circle {
    display: block;
    width: 94px;
    height: 94px;
    margin: 0 auto;
    border: 3px solid var(--gold);
    border-radius: 50%;
    box-sizing: border-box;
  }
  .brand-name {
    margin-top: 22px;
    font-size: 36px;
    font-weight: 400;
    letter-spacing: 1px;
    color: var(--gold);
    line-height: 1;
  }
  .divider {
    position: absolute;
    left: 313px;
    top: 72px;
    width: 1px;
    height: 200px;
    background: linear-gradient(to bottom, transparent, var(--divider) 20%, var(--divider) 80%, transparent);
  }
  .contact-block {
    position: absolute;
    left: 336px;
    top: 82px;
    color: var(--ink);
  }
  .person-name {
    margin: 0;
    font-size: 22px;
    font-weight: 700;
    color: var(--gold);
    line-height: 1.1;
  }
  .person-role {
    margin: 3px 0 0;
    font-size: 15.5px;
    line-height: 1.2;
  }
  .address {
    margin: 13px 0 0;
    font-size: 14.5px;
  }
  .contact-list {
    list-style: none;
    margin: 10px 0 0;
    padding: 0;
    font-size: 14.5px;
  }
  .contact-list li {
    display: flex;
    align-items: center;
    height: 23px;
  }
  .contact-icon {
    width: 16px;
    height: 16px;
    margin-right: 9px;
    fill: var(--gold);
  }
  .band {
    position: absolute;
    left: 0;
    bottom: 0;
    width: 600px;
    height: 22px;
  }

  /* Back */
  .card-back {
    left: 311px;
    top: 473px;
    background: radial-gradient(ellipse at 50% 35%, var(--gold-light) 0%, var(--gold-deep) 75%);
  }
  .back-mark {
    position: absolute;
    left: 211px;
    top: 80px;
    width: 178px;
    height: 178px;
    border: 4px solid var(--white);
    border-radius: 50%;
    box-sizing: border-box;
    display: flex;
    align-items: center;
    justify-content: center;
  }
  .back-name {
    font-size: 26px;
    font-weight: 400;
    letter-spacing: 2px;
    color: var(--white);
  }
  .back-url {
    position: absolute;
    left: 0;
    right: 0;
    top: 288px;
    text-align: center;
    font-size: 14px;
    letter-spacing: 3.5px;
    color: var(--white);
  }
</style>
</head>
<body>
<main class="canvas">

  <section class="card card-front" aria-label="Business card front">
    <div class="brand-block">
      <span class="brand-circle" aria-hidden="true"></span>
      <div class="brand-name">LORVANTI</div>
    </div>

    <div class="divider" aria-hidden="true"></div>

    <div class="contact-block">
      <h1 class="person-name">Dario Lorvanti</h1>
      <p class="person-role">CEO &amp; CO Founder</p>
      <p class="address">4817 E Halvern</p>
      <ul class="contact-list">
        <li>
          <svg class="contact-icon" viewBox="0 0 16 16" aria-hidden="true"><path d="M3.5 1.5l2.4 0.2 1 3.2-1.6 1.3c0.8 1.7 2 2.9 3.7 3.7l1.3-1.6 3.2 1v2.4c0 1-0.8 1.8-1.8 1.8C6.3 13.5 2.5 9.7 1.7 4.3 1.6 2.5 2.4 1.5 3.5 1.5z"/></svg>
          555-384-1926
        </li>
        <li>
          <svg class="contact-icon" viewBox="0 0 16 16" aria-hidden="true"><rect x="4" y="1.5" width="8" height="4" rx="0.5"/><rect x="1" y="6" width="14" height="6" rx="1"/><rect x="4" y="12.5" width="8" height="2.5"/></svg>
          555-384-1926
        </li>
        <li>
          <svg class="contact-icon" viewBox="0 0 16 16" aria-hidden="true"><path d="M1.5 3.5h13v9h-13z M2.5 4.5l5.5 4.2 5.5-4.2z" fill-rule="evenodd"/></svg>
          dario@lorvanti.com
        </li>
        <li>
          <svg class="contact-icon" viewBox="0 0 16 16" aria-hidden="true"><circle cx="8" cy="8" r="7"/><path d="M4 5c1.5 0 2 1 3 1.5S6.5 9 5 9.5 4 12 4 12M10 3c-1 1 0 2 1 2.5s1.5 2 0.5 3-0.5 3 0.5 3.5" stroke="#f3f3f3" stroke-width="1.2" fill="none"/></svg>
          LORVANTI.COM
        </li>
      </ul>
    </div>

    <svg class="band" viewBox="0 0 600 22" preserveAspectRatio="none" aria-hidden="true">
      <defs>
        <linearGradient id="bandGold" x1="0" x2="1" y1="0" y2="0">
          <stop offset="0" stop-color="#cfa53e"/>
          <stop offset="0.55" stop-color="#e4c564"/>
          <stop offset="1" stop-color="#d1a83f"/>
        </linearGradient>
      </defs>
      <polygon points="0,0 394,0 388,22 0,22" fill="url(#bandGold)"/>
      <polygon points="394,0 398,0 392,22 388,22" fill="#ffffff"/>
      <polygon points="398,0 600,0 600,22 392,22" fill="#7a7a7a"/>
    </svg>
  </section>

  <section class="card card-back" aria-label="Business card back">
    <div class="back-mark">
      <span class="back-name">LORVANTI</span>
    </div>
    <div class="back-url">www.lorvanti.com</div>
  </section>

</main>
</body>
</html>
```